BrindleStaffing Business Card Design

We are a staffing company finding positions for dedicated nurses and physicians.

Target Market(s)

Business Professionals

Industry/Entity Type

Staffing

Contact Information for Business Card

Gordon Pratley
Chairman
417 39th Avenue South
SAINT PETERSBURG FL 33712
813-555-4172 Mobile
813-555-8036 Fax
gpratley@brindlestaffing.com
www.brindlestaffing.com

Font styles to use
Sans Serif

Colors
fbee3e
f04a50
f37122

Requirements
Must have
• Logo Attached, see colors below. We'd like to see Yellow, Orange and Red.

```html
<!DOCTYPE html>
<html lang="en">
<head>
<meta charset="utf-8">
<title>BrindleStaffing Business Card</title>
<link rel="stylesheet" href="https://fonts.googleapis.com/css2?family=Roboto:wght@400;500;700&display=swap">
<style>
  :root {
    --stage: #2b2b2b;
    --brand-yellow: #fbee3e;
    --brand-orange: #f37122;
    --brand-red: #f04a50;
    --card-white: #ffffff;
    --text-on-brand: #ffffff;
  }
  html, body {
    margin: 0;
    padding: 0;
    width: 1125px;
    height: 1200px;
    overflow: hidden;
    background: var(--stage);
    font-family: "Roboto", Arial, sans-serif;
  }
  .canvas {
    position: relative;
    width: 1125px;
    height: 1200px;
  }
  .card {
    position: absolute;
    left: 150px;
    width: 825px;
    height: 470px;
    border-radius: 26px;
    overflow: hidden;
  }
  .card--front {
    top: 99px;
    background: var(--card-white);
  }
  .card--back {
    top: 631px;
    background: linear-gradient(135deg, var(--brand-orange) 0%, var(--brand-red) 100%);
  }
  .front-wave {
    position: absolute;
    inset: 0;
    width: 825px;
    height: 470px;
  }
  .contact-name {
    position: absolute;
    left: 42px;
    top: 90px;
    margin: 0;
    font-size: 29px;
    font-weight: 700;
    color: var(--text-on-brand);
    line-height: 1.1;
  }
  .contact-role {
    position: absolute;
    left: 43px;
    top: 124px;
    margin: 0;
    font-size: 20px;
    font-weight: 500;
    color: var(--text-on-brand);
  }
  .contact-address {
    position: absolute;
    left: 41px;
    top: 232px;
    margin: 0;
    font-style: normal;
    font-size: 19.5px;
    line-height: 25px;
    color: var(--text-on-brand);
  }
  .contact-list {
    position: absolute;
    left: 42px;
    top: 298px;
    margin: 0;
    padding: 0;
    list-style: none;
    color: var(--text-on-brand);
    font-size: 19.5px;
  }
  .contact-list li {
    display: flex;
    align-items: center;
    height: 26px;
  }
  .contact-icon {
    width: 18px;
    height: 18px;
    margin-right: 14px;
    flex: none;
  }
  .brand-lockup {
    position: absolute;
    display: flex;
    align-items: center;
    white-space: nowrap;
    transform: translate(-50%, -50%);
  }
  .brand-lockup--front {
    left: 608px;
    top: 240px;
    gap: 10px;
  }
  .brand-lockup--back {
    left: 412px;
    top: 252px;
    gap: 16px;
  }
  .brand-dot {
    flex: none;
    border-radius: 50%;
    background: var(--brand-yellow);
  }
  .brand-lockup--front .brand-dot {
    width: 18px;
    height: 18px;
    background: var(--brand-orange);
  }
  .brand-lockup--back .brand-dot {
    width: 28px;
    height: 28px;
  }
  .wordmark {
    margin: 0;
    font-weight: 700;
    letter-spacing: -0.5px;
    line-height: 1;
  }
  .wordmark--front {
    font-size: 46px;
    color: var(--brand-red);
  }
  .wordmark--back {
    font-size: 76px;
    color: var(--text-on-brand);
  }
</style>
</head>
<body>
<main class="canvas">
  <section class="card card--front" aria-label="Business card front">
    <svg class="front-wave" viewBox="0 0 825 470" aria-hidden="true">
      <defs>
        <linearGradient id="wave-fill" x1="0" y1="0" x2="1" y2="1">
          <stop offset="0" stop-color="#f37122"/>
          <stop offset="1" stop-color="#f04a50"/>
        </linearGradient>
        <filter id="wave-shadow" x="-10%" y="-10%" width="130%" height="130%">
          <feDropShadow dx="4" dy="2" stdDeviation="5" flood-color="#000" flood-opacity="0.3"/>
        </filter>
      </defs>
      <path filter="url(#wave-shadow)" fill="url(#wave-fill)"
        d="M0 0 H377 C330 20 295 60 315 120 C335 190 400 250 420 340 C430 400 405 440 371 470 H0 Z"/>
    </svg>

    <h1 class="contact-name">Gordon Pratley</h1>
    <p class="contact-role">Chairman</p>

    <address class="contact-address">
      417 39th Avenue South<br>
      SAINT PETERSBURG FL 33712
    </address>

    <ul class="contact-list">
      <li>
        <svg class="contact-icon" viewBox="0 0 18 18" aria-hidden="true">
          <rect x="4.5" y="1" width="9" height="16" rx="1.5" fill="none" stroke="#fff" stroke-width="1.8"/>
          <rect x="7.5" y="13.5" width="3" height="1.5" fill="#fff"/>
        </svg>
        813-555-4172
      </li>
      <li>
        <svg class="contact-icon" viewBox="0 0 18 18" aria-hidden="true">
          <rect x="4.5" y="1.5" width="9" height="5" fill="#fff"/>
          <rect x="1" y="7.5" width="16" height="7" rx="1.5" fill="#fff"/>
          <rect x="4" y="12" width="10" height="4.5" fill="#f25a3c" stroke="#fff" stroke-width="1.2"/>
        </svg>
        813-555-8036
      </li>
      <li>
        <svg class="contact-icon" viewBox="0 0 18 18" aria-hidden="true">
          <rect x="1.5" y="4" width="15" height="10" fill="none" stroke="#fff" stroke-width="1.6"/>
          <path d="M1.5 4 L9 10 L16.5 4" fill="none" stroke="#fff" stroke-width="1.6"/>
        </svg>
        gpratley@brindlestaffing.com
      </li>
      <li>
        <svg class="contact-icon" viewBox="0 0 18 18" aria-hidden="true">
          <circle cx="9" cy="9" r="7.5" fill="#fff"/>
          <path d="M5 5 C7 6 6 8 8 9 C9 10 8 12 9 14 M11 3.5 C12 5 14 5 14.5 7" fill="none" stroke="#f25a3c" stroke-width="1.6"/>
        </svg>
        www.brindlestaffing.com
      </li>
    </ul>

    <div class="brand-lockup brand-lockup--front">
      <span class="brand-dot" aria-hidden="true"></span>
      <p class="wordmark wordmark--front">BrindleStaffing</p>
    </div>
  </section>

  <section class="card card--back" aria-label="Business card back">
    <div class="brand-lockup brand-lockup--back">
      <span class="brand-dot" aria-hidden="true"></span>
      <p class="wordmark wordmark--back">BrindleStaffing</p>
    </div>
  </section>
</main>
</body>
</html>
```